BLS Business Card 2018

Larkmere Chiropractic. We have two locations that we want to advertise on the same card. Brightvale OrthoCore campus address: 3815 Pellham Dr., Suite 240, Flowood, MS 39417. Madison address: 246 Willowmere Dr., Building D., Madison, MS 39284. website: www.drlarkmere-example.com. o:(601)555-0147 f:(601)555-0183

Target Market(s)

Health care decision makers: primary care doctors and mothers

Contact Information for Business Card

I have no idea; up for any suggestions and I'd do much better picking from examples versus describing what I'm looking for. We are in a very high end location and would like the cards to look really sharp.

Requirements
Must have
• My name, Martin R Belvane, D.C.

```html
<!DOCTYPE html>
<html lang="en">
<head>
<meta charset="utf-8">
<title>Larkmere Chiropractic Business Card</title>
<link href="https://fonts.googleapis.com/css2?family=Cinzel:wght@400&family=Roboto:wght@300;400&family=Roboto+Condensed:wght@700&display=swap" rel="stylesheet">
<style>
  :root {
    --backdrop: #6e5238;
    --card-white: #f7f7f6;
    --card-black: #1c1d1e;
    --ink: #2a2a2a;
    --ink-soft: #555;
    --band: #141414;
    --on-dark: #eeeeee;
    --on-dark-soft: #c9c9c9;
  }
  html, body {
    margin: 0;
    padding: 0;
    overflow: hidden;
  }
  .canvas {
    position: relative;
    width: 1200px;
    height: 911px;
    background: var(--backdrop);
    overflow: hidden;
  }
  .card {
    position: absolute;
    width: 560px;
    height: 320px;
    box-shadow: 0 12px 30px rgba(0,0,0,0.35);
  }
  .card-front {
    left: 50px;
    top: 110px;
    background: var(--card-white);
    color: var(--ink);
  }
  .card-back {
    left: 590px;
    top: 480px;
    background: var(--card-black);
    color: var(--on-dark);
  }
  .brand {
    position: absolute;
    display: flex;
    align-items: center;
    gap: 12px;
  }
  .brand-mark {
    width: 34px;
    height: 34px;
    border-radius: 50%;
    border: 1.5px solid currentColor;
    flex: none;
  }
  .brand-name {
    font-family: "Cinzel", serif;
    font-weight: 400;
    line-height: 1;
    letter-spacing: 0.02em;
  }
  .brand-name span { display: block; }
  .card-front .brand { left: 44px; top: 52px; }
  .card-front .brand-name { font-size: 26px; }
  .card-front .brand-name span + span { font-size: 17px; margin-top: 3px; }

  .name-band {
    position: absolute;
    right: 0;
    top: 70px;
    width: 240px;
    height: 40px;
    background: var(--band);
    display: flex;
    align-items: center;
    justify-content: center;
    font-family: "Roboto Condensed", sans-serif;
    font-weight: 700;
    font-size: 17px;
    color: var(--on-dark);
    letter-spacing: 0.01em;
  }

  .contact {
    position: absolute;
    left: 44px;
    top: 128px;
    font-family: "Roboto", sans-serif;
    font-weight: 300;
    font-size: 11.5px;
    color: var(--ink-soft);
    line-height: 1.4;
  }
  .contact-line {
    display: flex;
    align-items: center;
    gap: 7px;
  }
  .contact-line svg { width: 10px; height: 10px; flex: none; fill: var(--ink); }
  .address { margin-top: 9px; }
  .address + .address { margin-top: 6px; }

  .card-back .brand { left: 250px; top: 180px; }
  .card-back .brand-name { font-size: 24px; }
  .card-back .brand-name span + span { font-size: 16px; margin-top: 3px; }
  .web {
    position: absolute;
    left: 296px;
    top: 240px;
    font-family: "Roboto", sans-serif;
    font-weight: 400;
    font-size: 11px;
    letter-spacing: 0.22em;
    color: var(--on-dark-soft);
  }
</style>
</head>
<body>
<div class="canvas">

  <section class="card card-front">
    <div class="brand">
      <div class="brand-mark"></div>
      <div class="brand-name"><span>LARKMERE</span><span>CHIROPRACTIC</span></div>
    </div>

    <div class="name-band">MARTIN R BELVANE, D.C.</div>

    <div class="contact">
      <div class="contact-line">
        <svg viewBox="0 0 10 10"><path d="M2 0.5 L3.6 2.6 L2.8 3.6 C3.4 5 4.8 6.4 6.2 7 L7.2 6.2 L9.4 7.8 L8.4 9.4 C4.4 9.2 0.8 5.6 0.6 1.6 Z"/></svg>
        <span>(601)555-0147</span>
      </div>
      <div class="contact-line">
        <svg viewBox="0 0 10 10"><rect x="2.5" y="0.5" width="5" height="3"/><rect x="0.5" y="3.5" width="9" height="4.5" rx="0.8"/><rect x="2.5" y="7" width="5" height="2.5"/></svg>
        <span>(601)555-0183</span>
      </div>
      <div class="contact-line">
        <svg viewBox="0 0 10 10"><circle cx="5" cy="5" r="4.5"/></svg>
        <span>www.drlarkmere-example.com</span>
      </div>
      <div class="address">Brightvale OrthoCore campus :<br>3815 Pellham Dr., Suite 240<br>Flowood, MS 39417.</div>
      <div class="address">Madison address:<br>246 Willowmere Dr., Building D.<br>Madison, MS 39284.</div>
    </div>
  </section>

  <section class="card card-back">
    <div class="brand">
      <div class="brand-mark"></div>
      <div class="brand-name"><span>LARKMERE</span><span>CHIROPRACTIC</span></div>
    </div>
    <div class="web">WWW.DRLARKMERE-EXAMPLE.COM</div>
  </section>

</div>
</body>
</html>
```